Business Cards for new orthopaedic surgery practice

My husband and I are starting our own orthopaedic surgery practice. We are looking for a business card that is uniform, but one will have my name/title and the other will have his. You can just create one design with my name on it for now. But when I choose your design as the winning design I will ask that you add another copy with his name/title.

We are looking for classy, simple, elite all in one. We like dark blues/a little gold/yellow. Something that goes with our logo. We want our logo incorporated. Here is all the info you need:
Business name: RV Bone & Vitality Center
Location: 38517 North Willowmere Ave
Larkfield Bay, FL 33409
Phone: 954-218-4063
Fax: 954-582-7341
Email: info@myrvbonecare.example

Names: Lydia Vance, M.D.
Board Certified Hand and Upper Extremity Surgeon

Ebo Dansu, M.D.
Board Certified Hip & Knee Replacement/General Orthopaedic Surgeon

Can decide what you want to put on the back. Maybe a slogan:
Built on trust. Devoted to you

I am just going to upload our logo. The only thing is if we select you as the winning design, the location, and phone numbers may change. We will need your help to update that once fully solidified.

Industry/Entity Type

Medical

Contact Information for Business Card

Colors
0054AA
0677BA
7BADD7
CADEEF
E8F1F8
0094D4
00A9DD
6FCCEA
C7EBF8
E9F6FB

Requirements
Must have
• class, appeal,
Should not have
• We want to air on the side of masculine if we are looking at masculine vs. feminine feel. But we still want it classy, sophisticated, and something we will love

```html
<!DOCTYPE html>
<html lang="en">
<head>
<meta charset="utf-8">
<title>RV Bone &amp; Vitality Center – Business Card</title>
<link href="https://fonts.googleapis.com/css2?family=Montserrat:wght@400;500;600;700&display=swap" rel="stylesheet">
<style>
  :root {
    --navy: #253e7f;
    --navy-deep: #1b2f63;
    --cyan: #17b9de;
    --white: #ffffff;
    --paper: #ffffff;
  }
  * { margin: 0; padding: 0; box-sizing: border-box; }
  html, body { width: 894px; height: 1200px; overflow: hidden; background: var(--paper); }
  body { position: relative; font-family: "Montserrat", Arial, sans-serif; }

  .card { position: absolute; left: 0; width: 894px; overflow: hidden; }
  .card-front { top: 0; height: 568px; }
  .card-back { top: 632px; height: 568px; background: var(--navy); }

  .front-shadow {
    position: absolute; left: 20px; top: 560px; width: 220px; height: 14px;
    box-shadow: 0 10px 18px rgba(90, 150, 150, 0.45);
    border-radius: 50%;
  }

  .card-art { position: absolute; inset: 0; }

  .front-brand {
    position: absolute; left: 60px; top: 172px;
    color: var(--navy); font-weight: 600; font-size: 27px; line-height: 1.12;
    letter-spacing: 0.5px; text-transform: uppercase;
  }

  .slogan {
    position: absolute; left: 466px; top: 234px; width: 360px;
    color: var(--white); font-weight: 700; font-size: 29px; line-height: 36px;
    letter-spacing: 0.6px; text-transform: uppercase;
  }
  .slogan span { display: block; white-space: nowrap; }
  .slogan .second { text-align: right; }

  .doctor { position: absolute; left: 87px; top: 100px; color: var(--white); }
  .doctor-name {
    font-weight: 700; font-size: 24px; letter-spacing: 0.8px;
    padding-bottom: 2px; border-bottom: 2px solid var(--white); display: inline-block;
  }
  .doctor-title { margin-top: 6px; font-size: 13.5px; font-weight: 500; letter-spacing: 0.3px; }

  .contact-list { position: absolute; left: 86px; top: 180px; list-style: none; color: var(--white); }
  .contact-item { position: relative; padding-left: 41px; font-size: 21px; font-weight: 500; letter-spacing: 0.3px; white-space: nowrap; }
  .contact-item .icon {
    position: absolute; left: 0; top: 50%; transform: translateY(-50%);
    width: 32px; height: 32px;
  }
  .contact-phone { height: 32px; line-height: 32px; }
  .contact-fax { height: 32px; line-height: 32px; margin-top: 22px; }
  .contact-email { height: 32px; line-height: 32px; margin-top: 19px; }
  .contact-address { margin-top: 20px; line-height: 27px; }

  .back-brand {
    position: absolute; left: 534px; top: 395px; width: 300px; text-align: center;
    color: var(--navy); font-weight: 600; font-size: 24px; line-height: 1.2;
    letter-spacing: 0.5px; text-transform: uppercase;
  }
</style>
</head>
<body>
  <div class="front-shadow"></div>

  <section class="card card-front">
    <svg class="card-art" width="894" height="568" viewBox="0 0 894 568" aria-hidden="true">
      <defs>
        <filter id="curve-shade" x="-20%" y="-20%" width="140%" height="140%">
          <feDropShadow dx="6" dy="4" stdDeviation="9" flood-color="#0d1c45" flood-opacity="0.5"/>
        </filter>
      </defs>
      <rect width="894" height="568" fill="var(--navy)"/>
      <path d="M336,357 C260,410 200,470 203,568 L894,568 L894,505 L363,505 Q313,505 313,449 C313,420 322,390 336,357 Z" fill="var(--cyan)"/>
      <path filter="url(#curve-shade)" d="M0,0 L211,0 C320,0 408,90 408,206 C408,270 380,320 336,357 C260,410 200,470 203,568 L0,568 Z" fill="var(--white)"/>
    </svg>
    <div class="front-brand">RV Bone &amp;<br>Vitality<br>Center</div>
    <p class="slogan"><span>“Built on trust.</span><span class="second">Devoted to you”</span></p>
  </section>

  <section class="card card-back">
    <svg class="card-art" width="894" height="568" viewBox="0 0 894 568" aria-hidden="true">
      <path d="M894,240 C690,250 450,330 285,568 L894,568 Z" fill="var(--white)"/>
    </svg>

    <div class="doctor">
      <h1 class="doctor-name">LYDIA VANCE, M.D.</h1>
      <p class="doctor-title">Board Certified Hand and Upper Extremity Surgeon</p>
    </div>

    <ul class="contact-list">
      <li class="contact-item contact-phone">
        <svg class="icon" viewBox="0 0 32 32" aria-hidden="true"><circle cx="16" cy="16" r="16" fill="#fff"/><path d="M11.5 8.5l2.6-.6 1.7 4-1.8 1.3c.9 2 2.4 3.5 4.4 4.4l1.3-1.8 4 1.7-.6 2.6c-.2.7-.8 1.2-1.5 1.2C14.8 21.3 10.7 17.2 10.3 10c0-.7.5-1.3 1.2-1.5z" fill="var(--navy)"/></svg>
        954-218-4063
      </li>
      <li class="contact-item contact-fax">
        <svg class="icon" viewBox="0 0 32 32" aria-hidden="true"><circle cx="16" cy="16" r="16" fill="#fff"/><rect x="11" y="8" width="10" height="5" fill="var(--navy)"/><rect x="8" y="13" width="16" height="8" rx="2" fill="var(--navy)"/><rect x="11" y="18" width="10" height="6" fill="var(--navy)" stroke="#fff" stroke-width="1.5"/></svg>
        954-582-7341
      </li>
      <li class="contact-item contact-email">
        <svg class="icon" viewBox="0 0 32 32" aria-hidden="true"><circle cx="16" cy="16" r="16" fill="#fff"/><rect x="8" y="10.5" width="16" height="11" fill="none" stroke="var(--navy)" stroke-width="2"/><path d="M8 10.5l8 6 8-6M8 21.5l6-5M24 21.5l-6-5" fill="none" stroke="var(--navy)" stroke-width="1.8"/></svg>
        info@myrvbonecare.example
      </li>
      <li class="contact-item contact-address">
        <svg class="icon" viewBox="0 0 32 32" aria-hidden="true"><circle cx="16" cy="16" r="16" fill="#fff"/><path d="M16 7a6 6 0 0 1 6 6c0 4.5-6 12-6 12s-6-7.5-6-12a6 6 0 0 1 6-6z" fill="var(--navy)"/><circle cx="16" cy="13" r="2.3" fill="#fff"/></svg>
        38517 North Willowmere Ave<br>Larkfield Bay, FL 33409
      </li>
    </ul>

    <div class="back-brand">RV Bone &amp; Vitality<br>Center</div>
  </section>
</body>
</html>
```